Roofing Company Realtor Marketing Flyer

We would like a design for marketing material aimed at realtors. We are seeking to build relationships with local realtors to ensure that both sellers and buyers are happy and confident with their roofing systems through roof inspections, No-Leak certification, roof repairs, and replacements if necessary.

There are three points that must be included:
1. Home inspectors are generalists. We are roof experts that specialize in diagnosing and fixing roofing problems.
2. We offer "No Leak" certification to offer peace of mind to homeowners.
3. We offer referral bonuses for realtors.

Target Market(s)

Realtors

Industry/Entity Type

Roofing

Font styles to use
Sans Serif

Colors

Designer to choose colors to be used in the design.

Requirements
Must have
• Must be double-sided.
• Must be similar to current marketing materials design. See website http://gablecrestpro.example and attached images for details.
• We would also like a "fanned out" version of our Sample Inspection Report showing glimpses of some of the images on the later pages (See attached documents).

```html
<!DOCTYPE html>
<html lang="en">
<head>
<meta charset="utf-8">
<title>Gable Crest — Realtor Flyer</title>
<link href="https://fonts.googleapis.com/css2?family=Lato:wght@400;700&family=Michroma&display=swap" rel="stylesheet">
<style>
  :root {
    --orange: #f08a2c;
    --orange-deep: #e9781a;
    --slate: #58585a;
    --slate-dark: #4a4a4c;
    --ink: #2f2f30;
    --paper: #ffffff;
    --mist: #f1f1f1;
    --backdrop: #e8e5e1;
  }
  * { box-sizing: border-box; margin: 0; padding: 0; }
  html, body { width: 1200px; height: 1200px; overflow: hidden; }
  body { background: var(--backdrop); font-family: "Lato", sans-serif; color: var(--ink); position: relative; }

  .page { position: absolute; top: 261px; width: 525px; height: 680px; background: var(--paper); overflow: hidden; box-shadow: 0 4px 14px rgba(0,0,0,.18); }
  .page--front { left: 47px; }
  .page--back { left: 629px; }

  .abs { position: absolute; }
  .photo { position: absolute; border: 1px solid #b9b9b9; box-shadow: 0 2px 4px rgba(0,0,0,.25); }

  .brand { position: absolute; color: var(--orange); font-family: "Lato", sans-serif; font-weight: 400; letter-spacing: .5px; white-space: nowrap; }

  /* front */
  .hero-photo { left: 0; top: 103px; width: 525px; height: 265px; border: 0; box-shadow: none;
    background: linear-gradient(180deg, #e6eff8 0%, #9cc2e6 22%, #7fb2e0 34%, #d8cdb9 55%, #c2b39a 72%, #4f8a3a 88%, #3b6e2a 100%); }
  .masthead { position: absolute; left: 0; top: 0; width: 525px; height: 140px; }
  .tagline { position: absolute; left: 40px; top: 94px; width: 230px; font-family: "Michroma", sans-serif; font-size: 13px; line-height: 20px; text-align: center; white-space: nowrap; }
  .tagline .dark { color: var(--slate-dark); display: block; padding-left: 26px; }
  .tagline .warm { color: var(--orange); display: block; }
  .promise { position: absolute; left: 0; top: 368px; width: 525px; height: 59px; background: var(--orange);
    color: #fff; font-family: "Michroma", sans-serif; font-size: 16.5px; line-height: 24px; text-align: center; padding-top: 6px; white-space: nowrap; }

  .service { position: absolute; top: 439px; width: 160px; text-align: center; }
  .service .photo { position: relative; display: block; margin: 0 auto; width: 114px; height: 94px; }
  .service p { font-size: 11px; line-height: 13px; margin-top: 11px; }
  .service--analysis { left: 21px; }
  .service--repair { left: 180px; }
  .service--replace { left: 340px; }

  .checklist { position: absolute; left: 0; top: 575px; width: 525px; height: 50px; background: var(--mist); }
  .check { position: absolute; display: flex; gap: 8px; font-size: 8.5px; line-height: 10.5px; }
  .check svg { flex: 0 0 10px; width: 10px; height: 10px; }
  .partner { position: absolute; left: 0; top: 632px; width: 525px; text-align: center; color: var(--orange-deep); font-size: 12.5px; font-weight: 700; }

  .contact-bar { position: absolute; left: 0; top: 654px; width: 525px; height: 26px; background: var(--slate);
    display: flex; justify-content: center; align-items: center; gap: 18px; color: #fff; font-size: 8.5px; }
  .contact-bar span { display: flex; align-items: center; gap: 6px; }
  .contact-bar svg { width: 9px; height: 9px; }

  /* back */
  .back-head { position: absolute; left: 0; top: 0; width: 525px; height: 124px; }
  .work-photo { top: 133px; width: 152px; height: 141px; }
  .feature { position: absolute; left: 26px; width: 478px; }
  .feature .photo { left: 0; top: 0; width: 113px; height: 80px; }
  .feature h3 { position: absolute; left: 127px; top: 0; font-size: 10.5px; font-weight: 700; white-space: nowrap; }
  .feature p { position: absolute; left: 127px; top: 18px; width: 347px; font-size: 7.6px; line-height: 10.3px; text-align: justify; }
  .badges { position: absolute; left: 0; top: 603px; width: 525px; height: 51px; background: var(--orange); }
  .badge { position: absolute; top: 7px; width: 38px; height: 38px; border-radius: 50%; border: 2px solid #fff; }
</style>
</head>
<body>

<section class="page page--front" aria-label="Flyer front">
  <div class="photo hero-photo" role="img" aria-label="Photo of a large two-storey stone house with a shingled roof, lawn and blue sky"></div>

  <svg class="masthead" viewBox="0 0 525 140" aria-hidden="true">
    <polygon points="0,0 525,0 525,92 284,92 142,14 0,110" fill="var(--slate)"/>
    <polygon points="0,123 142,22 282,98 282,103 180,140 0,140" fill="#ffffff"/>
    <polyline points="0,123 142,22 282,98 525,98" fill="none" stroke="var(--orange)" stroke-width="10" stroke-linejoin="miter"/>
  </svg>
  <div class="brand" style="left:268px; top:24px; font-size:42px;">Gable Crest</div>
  <div class="tagline"><span class="dark">BUYING OR</span><span class="warm">SELLING A HOUSE?</span></div>

  <div class="promise">WE CAN HELP PROTECT YOUR<br>INTERESTS &amp; ADD PROPERTY VALUE</div>

  <div class="service service--analysis">
    <div class="photo" role="img" aria-label="Photo of an inspector in a hard hat checking a shingled roof ridge" style="background:linear-gradient(160deg,#9a6a3c,#6f4a2a 60%,#3f3a33);"></div>
    <p>Roof Analysis &amp;<br>NO-LEAK Certification</p>
  </div>
  <div class="service service--repair">
    <div class="photo" role="img" aria-label="Photo of a roofer repairing damaged shingles" style="background:linear-gradient(160deg,#3b3b3d,#7a7876 55%,#a9a5a0);"></div>
    <p>Leak &amp;<br>Damage Repair</p>
  </div>
  <div class="service service--replace">
    <div class="photo" role="img" aria-label="Photo of a crew replacing a roof under blue sky" style="background:linear-gradient(180deg,#6aa4d8,#a9c7e4 45%,#e8e4dc 70%,#8a6b4b);"></div>
    <p>Roof Replacement</p>
  </div>

  <div class="checklist">
    <div class="check" style="left:34px; top:13px;">
      <svg viewBox="0 0 10 10"><rect x=".5" y="1.5" width="8" height="8" fill="none" stroke="var(--orange)"/><path d="M2.5 5.5l2 2L9.5 .8" fill="none" stroke="var(--orange)" stroke-width="1.3"/></svg>
      <span>Understand the true detail of the roof.</span>
    </div>
    <div class="check" style="left:34px; top:34px;">
      <svg viewBox="0 0 10 10"><rect x=".5" y="1.5" width="8" height="8" fill="none" stroke="var(--orange)"/><path d="M2.5 5.5l2 2L9.5 .8" fill="none" stroke="var(--orange)" stroke-width="1.3"/></svg>
      <span>Cover warranty gaps with our "No-Leak" Certification.</span>
    </div>
    <div class="check" style="left:277px; top:13px; width:240px;">
      <svg viewBox="0 0 10 10"><rect x=".5" y="1.5" width="8" height="8" fill="none" stroke="var(--orange)"/><path d="M2.5 5.5l2 2L9.5 .8" fill="none" stroke="var(--orange)" stroke-width="1.3"/></svg>
      <span>Our expert crews perform the repair and replacement services.</span>
    </div>
  </div>

  <div class="partner">Ask us about our partnership program!</div>

  <div class="contact-bar">
    <span><svg viewBox="0 0 10 10"><path d="M2 1l2 2-1 1.3c.6 1.2 1.5 2.1 2.7 2.7L7 6l2 2-1.3 1.5C4.5 9.3.7 5.5.5 2.3z" fill="var(--orange)"/></svg>800-555-0147</span>
    <span><svg viewBox="0 0 10 10"><rect x=".5" y="2" width="9" height="6.5" fill="var(--orange)"/><path d="M.5 2l4.5 3.5L9.5 2" fill="none" stroke="var(--slate)" stroke-width=".9"/></svg>info@gablecrestpro.example</span>
    <span><svg viewBox="0 0 10 10"><circle cx="5" cy="5" r="4.3" fill="none" stroke="var(--orange)"/><ellipse cx="5" cy="5" rx="1.8" ry="4.3" fill="none" stroke="var(--orange)" stroke-width=".8"/><path d="M.7 5h8.6" stroke="var(--orange)" stroke-width=".8"/></svg>www.gablecrestpro.example</span>
  </div>
</section>

<section class="page page--back" aria-label="Flyer back">
  <svg class="back-head" viewBox="0 0 525 124" aria-hidden="true">
    <rect width="525" height="122" fill="var(--slate)"/>
    <rect y="97" width="525" height="3" fill="#ffffff"/>
    <polygon points="0,100 288,100 276,112 0,112" fill="var(--orange)"/>
  </svg>
  <div class="brand" style="left:0; width:525px; text-align:center; top:34px; font-size:42px;">Gable Crest</div>

  <div class="photo work-photo" style="left:26px; background:linear-gradient(160deg,#b8b4ae,#6a4a3a 60%,#3c2f2a);" role="img" aria-label="Photo of a roofer nailing shingles with a nail gun"></div>
  <div class="photo work-photo" style="left:187px; background:linear-gradient(160deg,#6b9a3a,#2f6ab0 40%,#d98a5a 70%,#c8703e);" role="img" aria-label="Photo of hands fitting clay roof tiles"></div>
  <div class="photo work-photo" style="left:348px; background:linear-gradient(160deg,#6a4a38,#8f5a3c 45%,#c8c0b2 65%,#c84a30);" role="img" aria-label="Photo of two workers replacing a tiled roof on battens"></div>

  <svg class="abs" style="left:0; top:284px;" width="525" height="22" viewBox="0 0 525 22" aria-hidden="true">
    <rect width="525" height="22" fill="var(--slate)"/>
    <polygon points="250,22 265,9 525,9 525,22" fill="var(--orange)"/>
  </svg>

  <div class="feature" style="top:326px;">
    <div class="photo" role="img" aria-label="Photo of a shingled roof with vents and trees behind" style="background:linear-gradient(180deg,#5a8a3a,#aab0b4 35%,#8d9296);"></div>
    <h3>Understand the true detail of the roof</h3>
    <p>Home inspectors, who are generalists, are often unable to adequately inspect and assess the condition of roofing systems. GableCrest's specialists are trained to diagnose roofing problems and recommend solutions to fit any budget. Our expert Advisors carefully investigate all aspects of the roofing system to assess the condition of the roof. After completing the inspection, our Advisors compile a comprehensive report of their findings including images of the roofing system.</p>
  </div>

  <div class="feature" style="top:418px;">
    <div class="photo" role="img" aria-label="Photo of attic rafters and roof decking" style="background:linear-gradient(150deg,#3a2618,#8a5a36 50%,#c89a6a);"></div>
    <h3>Cover warranty gaps with our “No-Leak” Certification</h3>
    <p>Home warranties typically cover appliances, not roofing systems. What good is a warranty if it doesn't protect your property from top to bottom? Our "No-Leak" Certification provides peace of mind to homeowners</p>
  </div>

  <div class="feature" style="top:512px;">
    <div class="photo" role="img" aria-label="Photo of a brick house eave with gutter and downspout" style="background:linear-gradient(170deg,#9fb8d0,#6a7a8a 35%,#a85a3a 60%,#7a3a26);"></div>
    <h3>Our expert crews perform the repair &amp; replacement services</h3>
    <p>Repair and replacement services aren't just “jobs” to us. We take pride in every step of the process from quote to completion. Our dedicated office staff coordinates with our production team and technicians to ensure quality work and customer satisfaction.</p>
  </div>

  <div class="badges">
    <div class="badge" style="left:62px; background:#5aa83a;" role="img" aria-label="Eco-friendly badge"></div>
    <div class="badge" style="left:160px; background:#2a5aa8;" role="img" aria-label="Certified inspector badge"></div>
    <div class="badge" style="left:251px; background:#2a5aa8;" role="img" aria-label="Certified inspector badge"></div>
    <div class="badge" style="left:339px; background:#b8302a;" role="img" aria-label="Roof inspection association badge"></div>
    <div class="badge" style="left:427px; background:#d9802e;" role="img" aria-label="Home inspector association badge"></div>
  </div>

  <div class="contact-bar">
    <span><svg viewBox="0 0 10 10"><path d="M2 1l2 2-1 1.3c.6 1.2 1.5 2.1 2.7 2.7L7 6l2 2-1.3 1.5C4.5 9.3.7 5.5.5 2.3z" fill="var(--orange)"/></svg>800-555-0147</span>
    <span><svg viewBox="0 0 10 10"><rect x=".5" y="2" width="9" height="6.5" fill="var(--orange)"/><path d="M.5 2l4.5 3.5L9.5 2" fill="none" stroke="var(--slate)" stroke-width=".9"/></svg>info@gablecrestpro.example</span>
    <span><svg viewBox="0 0 10 10"><circle cx="5" cy="5" r="4.3" fill="none" stroke="var(--orange)"/><ellipse cx="5" cy="5" rx="1.8" ry="4.3" fill="none" stroke="var(--orange)" stroke-width=".8"/><path d="M.7 5h8.6" stroke="var(--orange)" stroke-width=".8"/></svg>www.gablecrestpro.example</span>
  </div>
</section>

</body>
</html>
```